Communication and Marketing agency needs a new presentation card

We are a group of communication and marketing agencies specialized in companies that are in the logistics and industrial sector. The head agency is TELVANO Grupo and the group consists of 4 agencies: TELVANO Media, TELVANO Digital, TELVANO Research and DifundeEnPantalla. We hace 4 offices in Spain (Madrid, Barcelona, Valencia and Murcia). We are looking for a clean and attractive design that transmits our experience, brand presence in the market and knowledge to those who receive the card.It has to maintain the colors of the logo that is attached.
Target Market(s)
logistics and industrial sector
Marketing department
Contact Information for Business Card
Clean and attractive design

```html
<!DOCTYPE html>
<html lang="en">
<head>
<meta charset="UTF-8">
<title>TELVANO Grupo – Business Card</title>
<link rel="stylesheet" href="https://fonts.googleapis.com/css2?family=Open+Sans:wght@400;600;700&display=swap">
<style>
  :root {
    --brand-red: #b21e23;
    --card-black: #262324;
    --paper-white: #ffffff;
    --stage: #e6e4e2;
    --shadow: rgba(0, 0, 0, 0.18);
  }
  * { box-sizing: border-box; margin: 0; padding: 0; }
  html, body { width: 1200px; height: 900px; overflow: hidden; }
  body {
    background: var(--stage);
    font-family: "Open Sans", Arial, sans-serif;
    position: relative;
  }
  .card {
    position: absolute;
    width: 600px;
    height: 343px;
    left: 300px;
    box-shadow: 0 10px 30px var(--shadow);
    overflow: hidden;
  }
  /* Front side */
  .card-front { top: 62px; background: var(--card-black); }
  .card-front .wordmark {
    position: absolute;
    left: 0; right: 0; top: 50%;
    transform: translateY(-50%);
    text-align: center;
    color: var(--brand-red);
    font-weight: 600;
    font-size: 46px;
    letter-spacing: 3px;
  }
  /* Back side */
  .card-back { top: 475px; background: var(--brand-red); color: var(--paper-white); }
  .card-back .wordmark {
    position: absolute;
    left: 34px; top: 92px;
    font-weight: 600;
    font-size: 34px;
    letter-spacing: 2px;
  }
  .holder {
    position: absolute;
    right: 34px; top: 48px;
    text-align: right;
  }
  .holder-name { font-weight: 700; font-size: 22px; letter-spacing: 0.5px; }
  .holder-role { font-size: 11px; letter-spacing: 6px; margin-top: 2px; }
  .contact-band {
    position: absolute;
    left: 0; right: 0; top: 190px;
    height: 78px;
    background: var(--paper-white);
    display: flex;
    justify-content: space-around;
    align-items: center;
    padding: 0 18px;
  }
  .contact-item {
    display: flex;
    flex-direction: column;
    align-items: center;
    gap: 6px;
    color: var(--brand-red);
    font-size: 15px;
  }
  .contact-icon {
    width: 22px; height: 22px;
    border-radius: 50%;
    background: var(--brand-red);
    display: flex; align-items: center; justify-content: center;
  }
  .agency-list {
    position: absolute;
    left: 34px; bottom: 22px;
    display: flex; gap: 22px;
    font-size: 11px; font-weight: 600;
  }
  .office-address {
    position: absolute;
    right: 34px; bottom: 20px;
    display: flex; align-items: center; gap: 6px;
    font-size: 15px;
  }
</style>
</head>
<body>

<section class="card card-front" aria-label="Business card front">
  <div class="wordmark">TELVANO Grupo</div>
</section>

<section class="card card-back" aria-label="Business card back">
  <div class="wordmark">TELVANO Grupo</div>

  <div class="holder">
    <div class="holder-name">YOUR NAME</div>
    <div class="holder-role">POSITION</div>
  </div>

  <div class="contact-band">
    <div class="contact-item">
      <span class="contact-icon">
        <svg width="12" height="9" viewBox="0 0 12 9"><rect x="0.5" y="0.5" width="11" height="8" fill="none" stroke="#fff"/><path d="M0.5 0.5 L6 5 L11.5 0.5" fill="none" stroke="#fff"/></svg>
      </span>
      <span>info@telvanogrupo.com</span>
    </div>
    <div class="contact-item">
      <span class="contact-icon">
        <svg width="12" height="12" viewBox="0 0 12 12"><path d="M2.5 1 L4.5 1 L5.2 3.6 L3.9 4.6 C4.6 6.2 5.8 7.4 7.4 8.1 L8.4 6.8 L11 7.5 L11 9.5 C11 10.3 10.3 11 9.5 11 C5 10.6 1.4 7 1 2.5 C1 1.7 1.7 1 2.5 1 Z" fill="#fff"/></svg>
      </span>
      <span>000-000-0000</span>
    </div>
    <div class="contact-item">
      <span class="contact-icon">
        <svg width="13" height="13" viewBox="0 0 13 13"><circle cx="6.5" cy="6.5" r="5.5" fill="none" stroke="#fff"/><ellipse cx="6.5" cy="6.5" rx="2.4" ry="5.5" fill="none" stroke="#fff"/><line x1="1" y1="6.5" x2="12" y2="6.5" stroke="#fff"/></svg>
      </span>
      <span>www.telvanogrupo.com</span>
    </div>
  </div>

  <div class="agency-list">
    <span class="agency">TELVANO Research</span>
    <span class="agency">TELVANO Digital</span>
    <span class="agency">TELVANO Media</span>
  </div>

  <div class="office-address">
    <svg width="10" height="14" viewBox="0 0 10 14"><path d="M5 0.5 C2.5 0.5 0.5 2.5 0.5 5 C0.5 8.5 5 13.5 5 13.5 C5 13.5 9.5 8.5 9.5 5 C9.5 2.5 7.5 0.5 5 0.5 Z" fill="#fff"/><circle cx="5" cy="5" r="1.8" fill="#b21e23"/></svg>
    <span>office address</span>
  </div>
</section>

</body>
</html>
```